Brightbay Orthodontics business card design

Need a business card design that reflects our re-branding (orthodontic office - braces) and a new partnership with a pediatric dental office. We would like to include "for adults and children" on the card as well so adults know they are welcome to get their braces here as well. Office design is modern and would like business card to reflect a modern type look. Here's the text we would like to be included on the card:

Darren Wolcott, DDS, MSD
5214 West Linden Avenue, Suite 204
Mansfield, TX 76991
555-418-2637
www.brightbayortho.example
info@brightbayortho.example

Can we add the following to the existing designs? Darren Wolcott, DDS, MSD 5214 West Linden Avenue, Suite 204 Mansfield, TX 76991 555-418-2637

Does anyone have any more vertical designs available? Thanks!

Dental

```html
<!DOCTYPE html>
<html lang="en">
<head>
<meta charset="utf-8">
<title>Brightbay Orthodontics business card</title>
<link href="https://fonts.googleapis.com/css2?family=Open+Sans:wght@400;600;700&display=swap" rel="stylesheet">
<style>
  :root {
    --page: #e9e7e4;
    --card: #0d0d0e;
    --card-top: #1d1e20;
    --ink: #f2f2f2;
    --muted: #c9cacc;
    --accent-blue: #4a86c5;
    --band-blue: #1f4f9c;
    --band-green: #7cc242;
    --rule: #3a3b3e;
  }
  * { margin: 0; padding: 0; box-sizing: border-box; }
  html, body { width: 1200px; height: 913px; overflow: hidden; }
  body {
    background: var(--page);
    font-family: "Open Sans", Arial, sans-serif;
    position: relative;
  }
  .card {
    position: absolute;
    width: 510px;
    height: 292px;
    background: radial-gradient(ellipse at 40% 20%, var(--card-top) 0%, var(--card) 70%);
    border-radius: 4px;
    box-shadow: 0 10px 24px rgba(0,0,0,.28);
    overflow: hidden;
  }
  .card-front { left: 55px; top: 310px; }
  .card-back { left: 635px; top: 310px; }

  .brand { display: flex; flex-direction: column; }
  .wordmark {
    color: var(--ink);
    font-weight: 700;
    letter-spacing: .2px;
    display: flex;
    align-items: center;
    gap: 12px;
    line-height: 1.05;
  }
  .wordmark .dot {
    width: 18px; height: 18px; border-radius: 50%;
    background: var(--ink);
    flex: none;
  }
  .tagline {
    color: var(--muted);
    font-weight: 400;
    letter-spacing: 1.5px;
    text-transform: uppercase;
  }
  .card-front .brand {
    position: absolute; left: 0; right: 0; top: 0; bottom: 0;
    justify-content: center; align-items: center; gap: 10px;
  }
  .card-front .wordmark { font-size: 34px; }
  .card-front .tagline { font-size: 12px; padding-left: 30px; }

  .card-back .brand {
    position: absolute; left: 26px; top: 148px; width: 220px; gap: 8px;
  }
  .card-back .wordmark { font-size: 21px; }
  .card-back .wordmark .dot { width: 12px; height: 12px; }
  .card-back .tagline { font-size: 9px; padding-left: 24px; letter-spacing: 1px; }

  .divider {
    position: absolute; left: 258px; top: 26px;
    width: 1px; height: 200px; background: var(--rule);
  }
  .contact {
    position: absolute; left: 282px; top: 30px; right: 14px;
    color: var(--ink);
    font-size: 11.5px;
    line-height: 1.55;
  }
  .contact .name { color: var(--accent-blue); font-size: 16px; font-weight: 600; line-height: 1.2; }
  .contact .degree { color: var(--muted); font-size: 11px; margin-bottom: 18px; }
  .contact .row { display: flex; align-items: center; gap: 8px; white-space: nowrap; }
  .contact .row svg { width: 10px; height: 10px; flex: none; fill: var(--muted); }
  .contact .web { color: var(--accent-blue); }
  .contact .address { margin-bottom: 2px; }

  .edge-band { position: absolute; left: 0; bottom: 0; width: 510px; height: 12px; }
</style>
</head>
<body>
  <section class="card card-front" aria-label="Card front">
    <div class="brand">
      <div class="wordmark"><span class="dot"></span><span>Brightbay Orthodontics</span></div>
      <div class="tagline">for adults and children</div>
    </div>
  </section>

  <section class="card card-back" aria-label="Card back">
    <div class="brand">
      <div class="wordmark"><span class="dot"></span><span>Brightbay Orthodontics</span></div>
      <div class="tagline">for adults and children</div>
    </div>
    <div class="divider"></div>
    <div class="contact">
      <div class="name">Darren Wolcott</div>
      <div class="degree">DDS, MSD</div>
      <div class="address">5214 West Linden Avenue<br>Suite 204, Mansfield, TX 76991</div>
      <div class="row"><svg viewBox="0 0 10 10"><path d="M2 1h2l1 2.5-1.2.8a6 6 0 0 0 2 2l.8-1.2L9 6v2c0 .6-.4 1-1 1A7.5 7.5 0 0 1 1 2c0-.6.4-1 1-1z"/></svg>555-418-2637</div>
      <div class="row web"><svg viewBox="0 0 10 10"><circle cx="5" cy="5" r="4.2" fill="none" stroke="#c9cacc" stroke-width="1"/><path d="M1 5h8M5 .8c-2 2.4-2 6 0 8.4M5 .8c2 2.4 2 6 0 8.4" fill="none" stroke="#c9cacc" stroke-width=".8"/></svg>www.brightbayortho.example</div>
      <div class="row"><svg viewBox="0 0 10 10"><rect x=".5" y="2" width="9" height="6.5" rx=".8"/><path d="M.8 2.4 5 5.6l4.2-3.2" fill="none" stroke="#0d0d0e" stroke-width=".9"/></svg>info@brightbayortho.example</div>
    </div>
    <svg class="edge-band" viewBox="0 0 510 12" preserveAspectRatio="none" aria-hidden="true">
      <polygon points="0,0 330,0 342,12 0,12" fill="var(--band-blue)"/>
      <polygon points="330,0 510,0 510,12 342,12" fill="var(--band-green)"/>
    </svg>
  </section>
</body>
</html>
```